We need a banner for this page on our website:
http://www.lucasfenwickinsights.com/pathways-in-australian-erp/

Dimensions of the image should be approximately 1200 × 500

We are a research-based consultancy and this is a banner to subscribe to our paid content (about corporate technology systems).

Would like the final design to incorporate logo (attached files).

Banner must include the title "Pathways in Australian ERP"

thanks

Target Market(s)

Business professionals within medium to large Australian organisations and technology companies.

Requirements
Nice to have
• a call to action. something like "subscribe now" or similar. Happy to be directed based on designers customer experience perspective.

Could potentially include "Lifetime Membership"

If including a person consider a male and a female - not one or the other.

```html
<!DOCTYPE html>
<html lang="en">
<head>
<meta charset="utf-8">
<title>Pathways in Australian ERP</title>
<link rel="stylesheet" href="https://fonts.googleapis.com/css2?family=Arimo:wght@400;700&display=swap">
<style>
  :root {
    --deep-blue: #0a3f7e;
    --mid-blue: #1577b8;
    --bright-cyan: #5fd3f5;
    --glow: #bff0ff;
    --brand-navy: #1c3f8e;
    --white: #ffffff;
    --cta-green-top: #5fd68a;
    --cta-green-bottom: #1f8a45;
    --hud: rgba(190, 240, 255, 0.75);
  }
  html, body {
    margin: 0;
    padding: 0;
    overflow: hidden;
    background: #ffffff;
  }
  .banner {
    position: relative;
    width: 1200px;
    height: 500px;
    overflow: hidden;
    font-family: "Arimo", Arial, sans-serif;
    background:
      radial-gradient(ellipse 520px 340px at 820px 230px, var(--glow) 0%, var(--bright-cyan) 28%, rgba(21,119,184,0) 75%),
      linear-gradient(100deg, #2a9bd0 0%, var(--mid-blue) 30%, #1b88c6 55%, var(--mid-blue) 80%, var(--deep-blue) 100%);
  }
  .banner__decor {
    position: absolute;
    inset: 0;
  }
  .brand {
    position: absolute;
    left: 40px;
    top: 58px;
    margin: 0;
    font-size: 27px;
    font-weight: 700;
    color: var(--brand-navy);
    letter-spacing: 0.5px;
  }
  .headline {
    position: absolute;
    left: 67px;
    top: 196px;
    margin: 0;
    font-size: 41px;
    line-height: 54px;
    font-weight: 400;
    color: var(--white);
  }
  .headline strong { font-weight: 700; }
  .cta {
    position: absolute;
    left: 404px;
    top: 366px;
    width: 198px;
    height: 40px;
    box-sizing: border-box;
    border: 3px solid var(--white);
    border-radius: 22px;
    background: linear-gradient(var(--cta-green-top), var(--cta-green-bottom));
    box-shadow: 0 3px 6px rgba(0, 30, 60, 0.45);
    display: flex;
    align-items: center;
    justify-content: center;
    gap: 8px;
    color: var(--white);
    font-size: 19px;
    font-weight: 700;
    text-decoration: none;
    text-shadow: 0 1px 1px rgba(0, 60, 20, 0.6);
  }
  .portrait {
    position: absolute;
    left: 715px;
    top: 92px;
    width: 380px;
    height: 408px;
    border-radius: 170px 170px 0 0;
    background: linear-gradient(180deg, rgba(30,40,60,0.55) 0%, rgba(220,190,175,0.75) 40%, rgba(255,255,255,0.92) 78%);
  }
</style>
</head>
<body>
  <main class="banner">
    <svg class="banner__decor" width="1200" height="500" viewBox="0 0 1200 500" aria-hidden="true">
      <g fill="none" stroke="rgba(220,248,255,0.35)">
        <circle cx="880" cy="250" r="235" stroke-width="2"/>
        <circle cx="880" cy="250" r="200" stroke-width="14" stroke="rgba(220,248,255,0.12)"/>
        <circle cx="880" cy="250" r="150" stroke-width="1.5"/>
      </g>
      <g class="hud-bars" fill="var(--hud)">
        <rect x="462" y="168" width="3" height="12"/><rect x="468" y="164" width="3" height="16"/>
        <rect x="474" y="170" width="3" height="10"/><rect x="480" y="162" width="3" height="18"/>
        <rect x="486" y="166" width="3" height="14"/><rect x="492" y="160" width="3" height="20"/>
        <rect x="498" y="167" width="3" height="13"/><rect x="504" y="163" width="3" height="17"/>
        <rect x="510" y="169" width="3" height="11"/><rect x="516" y="161" width="3" height="19"/>
        <rect x="522" y="165" width="3" height="15"/><rect x="528" y="159" width="3" height="21"/>
        <rect x="534" y="166" width="3" height="14"/><rect x="540" y="162" width="3" height="18"/>
        <rect x="546" y="158" width="3" height="22"/><rect x="552" y="164" width="3" height="16"/>
        <rect x="558" y="160" width="3" height="20"/><rect x="564" y="156" width="3" height="24"/>
        <rect x="570" y="158" width="3" height="22"/><rect x="576" y="152" width="3" height="28"/>
        <rect x="402" y="183" width="60" height="1.5"/>
      </g>
      <g class="hud-chart" fill="var(--hud)">
        <rect x="648" y="240" width="10" height="26"/>
        <rect x="662" y="228" width="10" height="38"/>
        <rect x="676" y="216" width="10" height="50"/>
        <rect x="690" y="222" width="10" height="44"/>
        <rect x="694" y="206" width="10" height="60" opacity="0.6"/>
        <rect x="648" y="208" width="45" height="2"/>
        <rect x="565" y="208" width="60" height="2"/>
        <rect x="735" y="208" width="60" height="2"/>
      </g>
      <polyline class="hud-line" points="740,265 752,258 760,262 770,250 780,254 790,240 798,236" fill="none" stroke="var(--hud)" stroke-width="1.5"/>
      <g fill="none" stroke="var(--hud)" stroke-width="2">
        <circle cx="595" cy="232" r="10"/>
        <circle cx="595" cy="232" r="3" fill="var(--hud)"/>
      </g>
      <rect role="img" aria-label="Stylised world map graphic" x="402" y="190" width="155" height="72" rx="14" fill="rgba(200,245,255,0.45)"/>
    </svg>

    <p class="brand">Lucas Fenwick Insights</p>

    <h1 class="headline">Pathways in<br>Australian <strong>ERP</strong></h1>

    <a class="cta" href="http://www.lucasfenwickinsights.com/pathways-in-australian-erp/">
      Subscribe Now
      <svg width="10" height="14" viewBox="0 0 10 14" aria-hidden="true"><polyline points="2,2 7,7 2,12" fill="none" stroke="#ffffff" stroke-width="3" stroke-linecap="round" stroke-linejoin="round"/></svg>
    </a>

    <div class="portrait" role="img" aria-label="Photo of a smiling business professional in a white shirt"></div>
  </main>
</body>
</html>
```